Calvanto Group Real Estate Company business cards

New business card design, we are generally happy with the basic layout of the existing front of business card, (feel free to change) but require a head shot photo on the back side.

http://www.calvanto.com.au/

Attached logos, and existing business card

------------------------------

Target Market(s)

Real estate

Industry/Entity Type

Real Estate

Contact Information for Business Card

Standard size double sided

Font styles to use
Other font styles liked:
• Futura

Requirements
Must have
• Photo head shot on the back side
Nice to have
• yes
Should not have
• No

```html
<!DOCTYPE html>
<html lang="en">
<head>
<meta charset="utf-8">
<title>Calvanto Group – Business Cards</title>
<link href="https://fonts.googleapis.com/css2?family=Jost:wght@400;500;600&display=swap" rel="stylesheet">
<style>
  :root {
    --page: #ecebef;
    --card: #2e2260;
    --ink: #ffffff;
    --accent: #f0901e;
    --muted: #b9b3d4;
    --photo-light: #f2f2f4;
    --photo-dark: #3a4258;
  }
  * { margin: 0; padding: 0; box-sizing: border-box; }
  html, body {
    width: 1200px; height: 900px; overflow: hidden;
    background: var(--page);
    font-family: "Jost", "Futura", sans-serif;
    color: var(--ink);
  }
  .card {
    position: absolute;
    left: 250px;
    width: 700px; height: 400px;
    background: var(--card);
    box-shadow: 0 10px 26px rgba(30, 20, 60, 0.25);
  }
  .card--photo { top: 40px; }
  .card--details { top: 470px; }

  /* Photo side */
  .headshot {
    position: absolute; left: 120px; top: 120px;
    width: 210px; height: 210px; border-radius: 50%;
    background: radial-gradient(circle at 50% 35%, var(--photo-light) 0 45%, var(--photo-dark) 100%);
  }
  .brand-block {
    position: absolute; right: 44px; top: 34px;
    text-align: center;
  }
  .wordmark {
    font-weight: 500; font-size: 46px; letter-spacing: 0.5px; line-height: 1;
    color: var(--ink); white-space: nowrap;
  }
  .tagline { font-size: 16px; margin-top: 8px; color: var(--ink); }
  .services { font-size: 16px; font-weight: 600; margin-top: 10px; letter-spacing: 0.5px; }

  /* Details side */
  .contact-block {
    position: absolute; left: 400px; top: 44px;
    font-size: 16px; line-height: 1.3;
  }
  .person-name { font-size: 22px; font-weight: 600; }
  .person-name .surname, .company .accent { color: var(--accent); }
  .person-role { font-size: 15px; }
  .company { font-size: 18px; font-weight: 600; margin-top: 16px; }
  .abn { font-size: 16px; font-weight: 500; }
  .contact-list { list-style: none; margin-top: 18px; }
  .contact-list li { display: flex; align-items: center; gap: 12px; margin-bottom: 5px; font-size: 16px; }
  .contact-list svg { width: 14px; height: 14px; flex: none; }
  .wordmark--large {
    position: absolute; left: 60px; bottom: 56px;
    font-size: 84px;
  }
</style>
</head>
<body>
  <section class="card card--photo">
    <div class="headshot" role="img" aria-label="Head shot photo of the agent in a suit"></div>
    <div class="brand-block">
      <div class="wordmark">calvanto group</div>
      <p class="tagline">let us show you property</p>
      <p class="services">Buy / Sell / Rent</p>
    </div>
  </section>

  <section class="card card--details">
    <div class="contact-block">
      <p class="person-name">Daniel <span class="surname">Tran</span></p>
      <p class="person-role">Director</p>
      <p class="company">Calvanto <span class="accent">Group</span></p>
      <p class="abn">ABN: 51 824 753 096</p>
      <ul class="contact-list">
        <li>
          <svg viewBox="0 0 16 16" aria-hidden="true"><path fill="#f0901e" d="M3.5 1.5l2.5 0 1 3.5-1.6 1.2a9 9 0 0 0 4.4 4.4L11 9l3.5 1v2.5c0 .8-.7 1.5-1.5 1.5C7 14 2 9 2 3c0-.8.7-1.5 1.5-1.5z"/></svg>
          0412 555 318
        </li>
        <li>
          <svg viewBox="0 0 16 16" aria-hidden="true"><rect x="1" y="3" width="14" height="10" fill="#f0901e"/><path d="M1.5 3.5L8 9l6.5-5.5" fill="none" stroke="#2e2260" stroke-width="1.3"/></svg>
          daniel.tran@calvanto.com.au
        </li>
        <li>
          <svg viewBox="0 0 16 16" aria-hidden="true"><circle cx="8" cy="8" r="7" fill="#f0901e"/><path d="M1 8h14M8 1c-3 3.5-3 10.5 0 14M8 1c3 3.5 3 10.5 0 14" fill="none" stroke="#2e2260" stroke-width="1"/></svg>
          www.calvanto.com.au
        </li>
      </ul>
    </div>
    <div class="wordmark wordmark--large">calvanto group</div>
  </section>
</body>
</html>
```